Corvane Freight Company Business Card Design

We are a company that delivers natural saltwater (from the ocean) to aquarium companies, restaurants and home marine tanks. I would like a new business card to suit.

Must include Name, company name, abn, contact number and website as well as logo (see attached).

Looking for a design that stands out, has a clean but unique appearance.

Double and single sided entries welcome

Business

• Logo

```html
<!DOCTYPE html>
<html lang="en">
<head>
<meta charset="utf-8">
<title>Corvane Freight Company – Business Card</title>
<link rel="stylesheet" href="https://fonts.googleapis.com/css2?family=Source+Sans+3:wght@400;600;700&display=swap">
<style>
  :root {
    --backdrop: #3a2f2a;
    --card-white: #ffffff;
    --brand-blue: #055cad;
    --brand-sky: #1e8fd6;
    --ink: #231f20;
    --card-edge: #c9d3de;
  }
  * { margin: 0; padding: 0; box-sizing: border-box; }
  html, body {
    width: 1200px;
    height: 471px;
    overflow: hidden;
    background: var(--backdrop);
    font-family: "Source Sans 3", "Myriad Pro", Arial, sans-serif;
  }
  .canvas { position: relative; width: 1200px; height: 471px; }

  .card {
    position: absolute;
    top: 85px;
    width: 524px;
    height: 298px;
    border-radius: 18px;
    overflow: hidden;
  }

  /* Front */
  .card-front { left: 40px; background: var(--card-white); }
  .front-brand {
    position: absolute;
    left: 30px;
    top: 72px;
    font-size: 34px;
    font-weight: 400;
    line-height: 1.05;
    color: var(--brand-sky);
    letter-spacing: -0.3px;
  }
  .holder {
    position: absolute;
    right: 46px;
    top: 161px;
    font-size: 16px;
    color: var(--brand-blue);
  }
  .holder-name { font-weight: 700; }
  .holder-title { font-weight: 400; font-size: 14px; }
  .divider {
    position: absolute;
    left: 0; right: 0;
    top: 185px;
    height: 2px;
    background: var(--brand-blue);
  }
  .contact {
    position: absolute;
    right: 46px;
    top: 194px;
    text-align: right;
    font-size: 13.5px;
    color: var(--ink);
    line-height: 22px;
    list-style: none;
  }
  .contact li { display: flex; justify-content: flex-end; align-items: center; gap: 6px; }
  .contact .icon { width: 11px; height: 11px; }
  .contact .address { margin-top: 8px; }

  /* Back */
  .card-back {
    left: 628px;
    background: var(--brand-blue);
    border: 1px solid var(--card-edge);
    display: flex;
    align-items: center;
    justify-content: center;
  }
  .back-brand {
    font-size: 52px;
    font-weight: 400;
    line-height: 1.02;
    color: var(--card-white);
    text-align: center;
    letter-spacing: -0.5px;
  }
</style>
</head>
<body>
<main class="canvas">
  <section class="card card-front" aria-label="Card front">
    <p class="front-brand">Corvane Freight<br>Company</p>
    <p class="holder"><span class="holder-name">Your Name,</span> <span class="holder-title">Title</span></p>
    <div class="divider"></div>
    <ul class="contact">
      <li>
        <svg class="icon" viewBox="0 0 12 12" aria-hidden="true"><path d="M3 1 L5 3.4 L3.9 4.6 Q5 7 7.4 8.1 L8.6 7 L11 9 L9.6 11 Q4.5 10.5 1 3 Z" fill="none" stroke="#231f20" stroke-width="1"/></svg>
        <span>123-456-7892</span>
      </li>
      <li>
        <svg class="icon" viewBox="0 0 12 12" aria-hidden="true"><g fill="none" stroke="#231f20" stroke-width="1"><circle cx="6" cy="6" r="5"/><ellipse cx="6" cy="6" rx="2.2" ry="5"/><path d="M1 6 H11 M2 3.3 H10 M2 8.7 H10"/></g></svg>
        <span>www.corvanefreight.com</span>
      </li>
      <li class="address">Street Name, City Name ,State, Zip Code</li>
      <li>ABN: 123456789</li>
    </ul>
  </section>

  <section class="card card-back" aria-label="Card back">
    <p class="back-brand">Corvane Freight<br>Company</p>
  </section>
</main>
</body>
</html>
```